Halvery Construction Group Website

Need a dynamic corporate website that can be built on with time. We want to get our information out to the world and have a place where customers can submit requests for proposals.

Target Market(s)

Custom home owners and buyers. Architects and Real Estate Agents.

Industry/Entity Type

Construction

Number of Pages Required

3 page

Font styles to use
Serif
Sans Serif

Requirements
Must have
• Company logo, about, company contact information, biography, contact, projects,
• Sleek, modern, clean, attractive design.
• Online form customers can use for filling out a request for project proposal.
• Linkedin hyperlink.
• Uses www.halveryconstructiongroup.example

```html
<!DOCTYPE html>
<html lang="en">
<head>
<meta charset="utf-8">
<title>Halvery Construction Group, Inc.</title>
<link rel="stylesheet" href="https://fonts.googleapis.com/css2?family=Questrial&family=Arimo:wght@400;700&display=swap">
<style>
:root{
  --navy:#262a72;
  --navy-deep:#22266f;
  --blue:#2f9ad6;
  --ink:#3b3b4a;
  --muted:#6d6d78;
  --page:#f9f9fa;
  --panel:#efeff1;
  --line:#d6d6dc;
  --white:#ffffff;
}
*{box-sizing:border-box;margin:0;padding:0}
html,body{width:1200px;height:2161px;overflow:hidden}
body{position:relative;background:var(--page);font-family:"Arimo",Arial,sans-serif;color:var(--muted)}
.abs{position:absolute}
.display{font-family:"Questrial",sans-serif;text-transform:uppercase}

/* header */
.brand{left:78px;top:22px;display:flex;align-items:center;gap:14px}
.brand-square{width:80px;height:76px;background:var(--navy)}
.brand-name{font-family:"Questrial",sans-serif;color:var(--navy);font-size:40px;line-height:1;letter-spacing:1px}
.brand-name small{display:block;font-size:15px;letter-spacing:.5px;margin-top:6px}
.call{left:670px;top:34px;display:flex;align-items:center;gap:14px}
.call-label{font-size:14px;color:var(--navy)}
.call-number{font-size:27px;color:var(--blue);margin-top:2px}
.quote-btn{left:925px;top:35px;width:197px;height:51px;display:flex;color:var(--white);font-size:19px}
.quote-btn span{flex:1;background:var(--navy);display:flex;align-items:center;justify-content:center}
.quote-btn i{width:38px;background:var(--blue);display:flex;align-items:center;justify-content:center}
.header-rule{left:0;top:112px;width:1200px;height:1px;background:#e4e4e8}

/* nav */
.nav{left:78px;top:128px;height:49px;display:flex;align-items:center;font-size:17px;color:#4a4a58}
.nav a{color:inherit;text-decoration:none;padding:0 30px;border-right:1px solid #ddd;line-height:28px}
.nav a:last-child{border:none}
.nav a.active{background:var(--navy);color:var(--white);height:49px;line-height:49px;padding:0 34px;border:none;margin-right:10px}
.search{left:1092px;top:134px}

/* hero */
.hero{left:0;top:187px;width:1200px;height:510px;background:linear-gradient(180deg,#b8cbe0 0%,#6f8fb8 35%,#8c97a3 70%,#5b6068 100%)}
.hero-title{left:0;top:345px;width:1200px;text-align:center;color:var(--white);font-size:62px;line-height:72px;text-shadow:0 2px 10px rgba(0,0,0,.45)}
.hero-btn{left:480px;top:510px;width:239px;height:57px;background:var(--navy);color:var(--white);font-size:20px;display:flex;align-items:center;justify-content:center}
.arrow{width:50px;height:50px;border:1.5px solid var(--white);border-radius:50%;display:flex;align-items:center;justify-content:center}

/* features */
.feature h3{font-family:"Questrial",sans-serif;text-transform:uppercase;color:var(--navy);font-weight:400;font-size:19px;margin-bottom:12px}
.feature p{font-size:14px;line-height:25px;width:245px;margin-bottom:6px}

/* projects */
.projects{left:78px;top:951px;width:1044px;height:472px;background:var(--panel);border-top:1px solid var(--line);border-bottom:1px solid var(--line)}
.section-title{color:var(--navy);font-size:37px;font-weight:400}
.projects .section-title{position:absolute;left:0;top:52px;width:100%;text-align:center}
.projects p{position:absolute;left:70px;top:108px;width:904px;text-align:center;font-size:13.5px;line-height:25px}
.thumb{top:171px;width:234px;height:167px}
.btn{background:var(--navy);color:var(--white);font-family:"Questrial",sans-serif;text-transform:uppercase;display:flex;align-items:center;justify-content:center;border-radius:3px}

/* welcome */
.welcome-kicker{left:78px;top:1488px;color:var(--blue);font-size:18px}
.welcome-title{left:78px;top:1518px;font-size:35px;color:var(--navy);white-space:nowrap}
.mark-area{left:78px;top:1583px;width:164px;height:157px;display:flex;align-items:center;justify-content:center;font-family:"Questrial",sans-serif;color:var(--navy);font-size:30px}
.copy{font-size:14px;line-height:27px}

/* quote form */
.quote-card{left:790px;top:1485px;width:332px;height:405px;border:1.5px solid var(--navy);background:var(--panel)}
.quote-card h2{position:absolute;left:0;top:22px;width:100%;text-align:center;color:var(--white);font-size:25px;font-weight:400}
.field{position:absolute;left:16px;width:300px;border:1px solid #9a9aa6;background:var(--page);font-size:14px;color:#4a4a58;padding:0 14px;display:flex;justify-content:space-between;align-items:center}

/* footer */
.footer{left:0;top:1948px;width:1200px;height:213px;background:var(--navy-deep);color:var(--white)}
.fnav{position:absolute;left:78px;top:20px;display:flex;align-items:center;font-size:15px}
.fnav span{padding:0 23px}
.fnav span.active{border:1px solid var(--blue);color:var(--blue);padding:14px 23px;margin-right:0}
.social{position:absolute;top:22px;width:42px;height:42px;border-radius:50%;border:1.5px solid var(--blue)}
.frule{position:absolute;left:0;top:90px;width:1200px;height:1px;background:#343a88}
.ficon{position:absolute;top:137px;width:50px;height:50px;border-radius:50%;display:flex;align-items:center;justify-content:center}
.ftext{position:absolute;font-size:14px;line-height:21px}
</style>
</head>
<body>

<header>
  <div class="abs brand">
    <div class="brand-square"></div>
    <div class="brand-name">HALVERY<small>CONSTRUCTION GROUP, INC.</small></div>
  </div>
  <div class="abs call">
    <svg width="44" height="44" viewBox="0 0 24 24"><path fill="#2f9ad6" d="M6.6 10.8a15.1 15.1 0 0 0 6.6 6.6l2.2-2.2c.3-.3.7-.4 1-.2 1.1.4 2.3.6 3.6.6.6 0 1 .4 1 1V20c0 .6-.4 1-1 1A17 17 0 0 1 3 4c0-.6.4-1 1-1h3.5c.6 0 1 .4 1 1 0 1.2.2 2.4.6 3.6.1.3 0 .7-.2 1z"/></svg>
    <div><div class="call-label">Call Us Know</div><div class="call-number">555 014 2290</div></div>
  </div>
  <div class="abs quote-btn display"><span>Get a Quote</span><i><svg width="16" height="16" viewBox="0 0 16 16" fill="none" stroke="#fff" stroke-width="2"><path d="M3 3l5 5-5 5M8 3l5 5-5 5"/></svg></i></div>
  <div class="abs header-rule"></div>

  <nav class="abs nav display">
    <a class="active" href="#">Home</a><a href="#">About</a><a href="#">Services</a><a href="#">Biography</a><a href="#">Projects</a><a href="#">Contcat Us</a>
  </nav>
  <svg class="abs search" width="26" height="26" viewBox="0 0 24 24" fill="none" stroke="#262a72" stroke-width="3"><circle cx="10" cy="10" r="7"/><path d="M15 15l6 6"/></svg>
</header>

<section>
  <div class="abs hero" role="img" aria-label="Photograph of a modern glass office tower and low commercial buildings on a busy street"></div>
  <h1 class="abs hero-title display" style="font-weight:400">Lorem Ipsum is Simple<br>Dummy Text</h1>
  <div class="abs hero-btn display">Contact Us Know</div>
  <div class="abs arrow" style="left:13px;top:403px"><svg width="16" height="20" viewBox="0 0 16 20" fill="none" stroke="#fff" stroke-width="2"><path d="M11 2L3 10l8 8"/></svg></div>
  <div class="abs arrow" style="left:1137px;top:403px"><svg width="16" height="20" viewBox="0 0 16 20" fill="none" stroke="#fff" stroke-width="2"><path d="M5 2l8 8-8 8"/></svg></div>
</section>

<section>
  <svg class="abs" style="left:88px;top:762px" width="62" height="56" viewBox="0 0 62 56"><path fill="#262a72" d="M31 2L2 28h8v26h16V38h10v16h16V28h8z"/></svg>
  <div class="abs feature" style="left:170px;top:755px"><h3>Lorem Ipsum is Text</h3><p>Lorem Ipsum is simply dummy text of the printing and industry.</p><p>Lorem Ipsum is simply dummy text of the printing and typesetting.</p></div>

  <svg class="abs" style="left:432px;top:762px" width="70" height="70" viewBox="0 0 70 70" fill="none" stroke="#262a72" stroke-width="3"><path d="M14 68V4M4 10h48M14 4l10 6M46 10v14M8 68h14"/><rect x="38" y="30" width="26" height="38"/><path d="M44 38h4M54 38h4M44 48h4M54 48h4M44 58h4M54 58h4"/></svg>
  <div class="abs feature" style="left:515px;top:755px"><h3>Lorem Ipsum is Text</h3><p>Lorem Ipsum is simply dummy text of the printing and industry.</p><p>Lorem Ipsum is simply dummy text of the printing and typesetting.</p></div>

  <svg class="abs" style="left:788px;top:762px" width="66" height="58" viewBox="0 0 66 58"><path fill="#262a72" d="M30 2L2 24h7v32h34V24h8zM48 8h8v14l-8-6z"/><rect x="16" y="30" width="8" height="8" fill="#f9f9fa"/><rect x="28" y="34" width="9" height="22" fill="#f9f9fa"/><path fill="#262a72" d="M46 38h18v18H46z"/></svg>
  <div class="abs feature" style="left:872px;top:755px"><h3>Lorem Ipsum is Text</h3><p>Lorem Ipsum is simply dummy text of the printing and industry.</p><p>Lorem Ipsum is simply dummy text of the printing and typesetting.</p></div>
</section>

<section class="abs projects">
  <h2 class="section-title display">Our Projects</h2>
  <p>Lorem Ipsum is simply dummy text of the printing and typesetting industry. Lorem Ipsum has been the industry's standard dummy text ever since the when an unknown has been the industry's standard dummy text ever since the</p>
  <div class="abs thumb" style="left:46px;background:linear-gradient(160deg,#4b79b8,#c9d4e0 60%,#8d9299)" role="img" aria-label="Project photo: white curved modern building"></div>
  <div class="abs thumb" style="left:286px;background:linear-gradient(170deg,#9fb6cf,#c8cbcf 50%,#5d6c68)" role="img" aria-label="Project photo: glass office block with trees"></div>
  <div class="abs thumb" style="left:526px;background:linear-gradient(160deg,#5e7fa8,#c9a774 55%,#4d4a4a)" role="img" aria-label="Project photo: glass tower at sunset"></div>
  <div class="abs thumb" style="left:764px;background:linear-gradient(170deg,#7aa0c8,#b8bdbf 55%,#5a5f63)" role="img" aria-label="Project photo: curved mall building on a road"></div>
  <div class="abs btn" style="left:449px;top:353px;width:146px;height:57px;font-size:18px">View All</div>
</section>

<section>
  <div class="abs welcome-kicker display">Welcome To</div>
  <h2 class="abs welcome-title display" style="font-weight:400">Halvery Construction Group, Inc.</h2>
  <div class="abs mark-area">HALVERY</div>
  <p class="abs copy" style="left:270px;top:1588px;width:490px">Lorem Ipsum is simply dummy text of the printing and typesetting industry. Lorem Ipsum has been the industry's standard dummy text ever since the 1500s, when an unknown printer took a galley of type and scrambled it to make a type specimen book. It has survived not only five centuries, but also the leap into electronic typesetting, remaining essentially unchanged. It was popularised in the 1960s with the release of Letraset.</p>
  <p class="abs copy" style="left:78px;top:1760px;width:690px">Lorem Ipsum is simply dummy text of the printing and typesetting industry. Lorem Ipsum has been the industry's standard dummy text ever since the 1500s.</p>
  <div class="abs btn" style="left:78px;top:1828px;width:171px;height:57px;font-size:20px">Know More</div>

  <form class="abs quote-card">
    <svg class="abs" style="left:-1px;top:-1px" width="332" height="96" viewBox="0 0 332 96"><path fill="#262a72" d="M0 0h332v56L166 96 0 56z"/></svg>
    <h2 class="display">Get a Quote</h2>
    <div class="field" style="top:118px;height:46px">Name<svg width="10" height="12" viewBox="0 0 10 12"><circle cx="5" cy="3" r="3" fill="#555"/><path d="M0 12a5 5 0 0 1 10 0z" fill="#555"/></svg></div>
    <div class="field" style="top:168px;height:47px">Email<svg width="12" height="9" viewBox="0 0 12 9"><rect width="12" height="9" fill="#555"/><path d="M0 0l6 5 6-5" stroke="#f9f9fa" fill="none"/></svg></div>
    <div class="field" style="top:220px;height:98px;align-items:flex-start;padding-top:14px">Message<svg width="13" height="11" viewBox="0 0 13 11"><ellipse cx="6.5" cy="4.5" rx="6.5" ry="4.5" fill="#555"/><path d="M2 7l-1 4 5-3z" fill="#555"/></svg></div>
    <div class="abs btn" style="left:95px;top:329px;width:145px;height:56px;font-size:20px">Submit</div>
  </form>
</section>

<footer class="abs footer">
  <div class="fnav"><span class="active">Home</span><span>About</span><span>Services</span><span>Biography</span><span>Projects</span><span>Contact</span></div>
  <div class="social" style="left:978px;background:var(--blue)" aria-label="Social link"></div>
  <div class="social" style="left:1029px" aria-label="Social link"></div>
  <div class="social" style="left:1080px" aria-label="Social link"></div>
  <div class="frule"></div>
  <div class="ftext display" style="left:80px;top:107px;font-size:16px">Contact Us</div>

  <div class="ficon" style="left:77px;background:var(--blue)"><svg width="18" height="24" viewBox="0 0 18 24"><path fill="#fff" d="M9 0a9 9 0 0 0-9 9c0 7 9 15 9 15s9-8 9-15a9 9 0 0 0-9-9zm0 12a3 3 0 1 1 0-6 3 3 0 0 1 0 6z"/></svg></div>
  <div class="ftext" style="left:143px;top:150px">101 - Lorem ipsum is simple<br>dummytext of print.</div>

  <div class="ficon" style="left:356px;border:1.5px solid var(--blue)"><svg width="20" height="20" viewBox="0 0 24 24"><path fill="#2f9ad6" d="M6.6 10.8a15.1 15.1 0 0 0 6.6 6.6l2.2-2.2c.3-.3.7-.4 1-.2 1.1.4 2.3.6 3.6.6.6 0 1 .4 1 1V20c0 .6-.4 1-1 1A17 17 0 0 1 3 4c0-.6.4-1 1-1h3.5c.6 0 1 .4 1 1 0 1.2.2 2.4.6 3.6.1.3 0 .7-.2 1z"/></svg></div>
  <div class="ftext" style="left:425px;top:151px">555 014 2290</div>

  <div class="ficon" style="left:609px;border:1.5px solid var(--blue)"><svg width="22" height="16" viewBox="0 0 22 16"><rect width="22" height="16" rx="2" fill="#2f9ad6"/><path d="M1 1l10 8 10-8" stroke="#22266f" stroke-width="1.8" fill="none"/></svg></div>
  <div class="ftext" style="left:680px;top:149px">info@halvery.example</div>

  <div class="ftext" style="left:876px;top:150px">©<span style="color:var(--blue)">HALVERY</span> - 2016, All rights<br>resreved.</div>
</footer>

</body>
</html>
```